Website for IT consulting Company

I need a website upgrade, the existing site content is ok, I would also like to add a testimonial page, the site should be something that is easy for us to update content. You use the content from www.kelvanbrook.com as an example. I will also post update logo and artwork. I also need a contact form with some type of validation or captcha.

I added Coded to the Project

Please omit Address maps

Target Market(s)

small business, service oriented companies. We provide IT Consulting, support and mangement

Industry/Entity Type

Information Technology

Coding

Number of Pages Required

1 page

Font styles to use
Serif
Sans Serif

Requirements
Must have
• Contain logo attached, and content from existing web site www.kelvanbrook.com.
• Also need to update content easily, and be movable to different platforms.
• There is a catch phrase
• "Let us worry about your technology…” “ so you don’t have to!”
• Should be included.
Nice to have
• Testimonial page, Project page where we can post new and past projects and pictures
Should not have
• none

```html
<!DOCTYPE html>
<html lang="en">
<head>
<meta charset="utf-8">
<title>Kelvanbrook Development Group, Inc — IT Consulting</title>
<link rel="stylesheet" href="https://fonts.googleapis.com/css2?family=Exo+2:ital,wght@0,600;0,700;0,800;1,700;1,800&family=Arimo:ital,wght@0,400;0,700;1,400&family=Tinos&display=swap">
<style>
:root{
  --black:#050505;
  --blue:#1f8fd6;
  --blue-dark:#0f6fb6;
  --blue-light:#2aa7e4;
  --ink:#1b1b1b;
  --grey-bg:#f3f3f3;
  --grey-bg2:#e9e9e9;
  --grey-arc:#9b9b9b;
  --footer:#23262b;
  --white:#ffffff;
  --muted:#cfd3d8;
}
*{box-sizing:border-box;margin:0;padding:0}
html,body{width:1200px;height:2612px;overflow:hidden;background:var(--white)}
body{position:relative;font-family:"Arimo",Arial,sans-serif;color:var(--ink)}
.abs{position:absolute}
.heading{font-family:"Exo 2",sans-serif;font-weight:800;font-style:italic;text-transform:uppercase;letter-spacing:.5px}

/* header */
.site-header{position:absolute;left:0;top:0;width:1200px;height:125px;background:var(--black)}
.brand{position:absolute;left:84px;top:38px;display:flex;align-items:center;gap:14px}
.brand-square{width:40px;height:40px;background:var(--blue);border-radius:6px}
.brand-name{font-family:"Exo 2",sans-serif;font-weight:800;font-size:44px;color:var(--white);letter-spacing:1px}
.follow{position:absolute;right:90px;top:16px;display:flex;align-items:center;gap:8px;color:var(--white);font-family:"Exo 2",sans-serif;font-weight:700;font-style:italic;font-size:18px}
.follow .label{margin-right:6px}
.social{width:26px;height:26px;background:#8a8a8a;border-radius:3px}
.header-contact{position:absolute;right:80px;top:66px;display:flex;align-items:center;gap:12px;color:var(--white);font-family:"Exo 2",sans-serif;font-weight:700;font-style:italic;font-size:21px}
.icon-box{width:38px;height:38px;background:var(--blue);border-radius:4px;display:flex;align-items:center;justify-content:center}
.header-contact .support{font-size:18px;margin-left:6px}

/* nav */
.main-nav{position:absolute;left:0;top:125px;width:1200px;height:55px;background:linear-gradient(#35aef0,#1a85cc)}
.main-nav a{position:absolute;top:16px;color:var(--white);text-decoration:none;font-family:"Exo 2",sans-serif;font-weight:800;font-style:italic;font-size:19px;letter-spacing:.6px}
.main-nav a.active{color:#1d3550}

/* hero */
.hero{position:absolute;left:0;top:180px;width:1200px;height:535px;background:linear-gradient(180deg,#6e7a86 0%,#4d5561 45%,#3a3b3d 75%,#5a4436 100%)}
.hero-tag{position:absolute;left:0;width:1200px;text-align:center;font-family:"Exo 2",sans-serif;font-weight:800;font-style:italic}
.hero-tag.one{top:288px;font-size:33px;color:var(--white)}
.hero-tag.two{top:340px;font-size:35px;color:var(--blue-light)}
.hero-dots{position:absolute;left:570px;top:513px;display:flex;gap:4px}
.hero-dots span{width:10px;height:10px;background:#9a9a9a}
.hero-dots span.on{background:var(--white)}

/* welcome */
.welcome{position:absolute;left:0;top:715px;width:1200px;height:295px;background:var(--white);text-align:center}
.section-title{position:absolute;left:0;width:1200px;text-align:center;font-family:"Exo 2",sans-serif;font-weight:800;font-style:italic;font-size:29px;text-transform:uppercase;letter-spacing:.6px;color:var(--ink)}
.section-title em{font-style:italic;color:var(--blue)}
.welcome .section-title{top:38px;font-size:27px}
.welcome p{position:absolute;left:95px;top:106px;width:1010px;font-size:13.4px;line-height:25px;color:#222}
.btn-more{position:absolute;left:530px;top:210px;width:151px;height:38px;background:var(--blue);color:var(--white);font-family:"Tinos",serif;font-size:17px;line-height:38px;text-align:center}
.title-rule{position:absolute;left:561px;width:78px;height:3px;background:var(--blue)}

/* services */
.services{position:absolute;left:0;top:1010px;width:1200px;height:572px;background:var(--grey-bg)}
.services .section-title{top:44px}
.services svg{position:absolute;left:0;top:0}
.svc-label{font-family:"Exo 2",sans-serif;font-weight:800;font-size:15.5px;fill:var(--ink);letter-spacing:.4px}

/* IT support */
.support{position:absolute;left:0;top:1582px;width:1200px;height:300px;background:linear-gradient(180deg,#25a2e4,#1576c1)}
.support .section-title{top:48px;color:var(--ink)}
.support .section-title em{color:var(--white)}
.support .title-rule{top:96px;background:var(--white)}
.card{position:absolute;top:145px;width:330px;height:92px;display:flex;gap:12px}
.card-photo{width:102px;height:92px;flex:none;border:3px solid var(--white)}
.card h3{font-family:"Exo 2",sans-serif;font-weight:800;font-style:italic;font-size:16px;line-height:19px;color:#1d3550;margin-top:6px}
.card p{font-size:13.5px;line-height:19px;color:var(--white);margin-top:3px}
.slide-arrow{position:absolute}

/* testimonials */
.testimonials{position:absolute;left:0;top:1882px;width:1200px;height:361px;background:var(--grey-bg2)}
.testimonials .section-title{top:48px}
.testimonials .title-rule{top:96px}
.quote{position:absolute;left:200px;top:136px;width:800px;text-align:center;font-style:italic;font-size:15.3px;line-height:29px;color:#222}
.quote-mark{position:absolute;font-family:"Tinos",serif;font-size:48px;color:#b9b9b9;line-height:1}
.author{position:absolute;left:0;width:1200px;text-align:center;font-weight:700}
.author.name{top:254px;font-size:17px}
.author.place{top:280px;font-size:14px}

/* footer */
.site-footer{position:absolute;left:0;top:2243px;width:1200px;height:325px;background:linear-gradient(180deg,#30343a,#1d2025)}
.foot-title{position:absolute;top:58px;font-family:"Exo 2",sans-serif;font-weight:800;font-style:italic;font-size:18px;color:var(--white)}
.foot-title em{color:var(--blue)}
.foot-rule{position:absolute;top:86px;height:1px;background:#4a4f57}
.quick-links{position:absolute;left:85px;top:100px;list-style:none}
.quick-links li{font-size:13.5px;line-height:25px;color:var(--white);padding-left:17px;position:relative}
.quick-links li::before{content:"";position:absolute;left:0;top:10px;width:4px;height:4px;border-radius:50%;background:var(--blue)}
.contact-block{position:absolute;left:286px;top:100px;color:var(--white);font-size:13.5px;line-height:22px}
.contact-row{display:flex;align-items:center;gap:14px;margin-top:12px}
.form-field{position:absolute;left:600px;width:225px;background:var(--white);border:1px solid #bbb;font-size:12px;padding:5px 6px;color:#222}
.btn-submit{position:absolute;left:604px;top:250px;width:89px;height:25px;background:var(--blue);color:var(--white);font-family:"Exo 2",sans-serif;font-weight:800;font-size:14px;text-align:center;line-height:25px;letter-spacing:.5px}
.foot-brand{position:absolute;left:905px;top:148px;display:flex;align-items:center;gap:12px}
.foot-brand .brand-square{width:36px;height:36px}
.foot-brand span{font-family:"Exo 2",sans-serif;font-weight:800;font-size:28px;color:var(--white)}

.bottom-bar{position:absolute;left:0;top:2568px;width:1200px;height:44px;background:linear-gradient(#2aa3e6,#1781cb)}
.copyright{position:absolute;left:86px;top:14px;font-family:"Exo 2",sans-serif;font-weight:800;font-style:italic;font-size:14px;color:var(--white)}
.bottom-follow{position:absolute;right:62px;top:9px;display:flex;align-items:center;gap:8px;font-family:"Exo 2",sans-serif;font-weight:800;font-style:italic;font-size:18px;color:var(--white)}
.bottom-follow .social{background:#7fb4dc}
</style>
</head>
<body>

<header class="site-header">
  <div class="brand"><span class="brand-square"></span><span class="brand-name">KELVANBROOK</span></div>
  <div class="follow"><span class="label">Follow Us On</span><span class="social"></span><span class="social"></span><span class="social"></span><span class="social"></span></div>
  <div class="header-contact">
    <span class="icon-box"><svg width="20" height="20" viewBox="0 0 24 24"><path fill="#fff" d="M6.6 10.8a15 15 0 0 0 6.6 6.6l2.2-2.2c.3-.3.7-.4 1-.2 1.1.4 2.3.6 3.6.6.6 0 1 .4 1 1V20c0 .6-.4 1-1 1A17 17 0 0 1 3 4c0-.6.4-1 1-1h3.5c.6 0 1 .4 1 1 0 1.3.2 2.5.6 3.6.1.3 0 .7-.2 1z"/></svg></span>
    <span>(713) 555-0148</span>
    <span class="icon-box" style="margin-left:10px"><svg width="22" height="22" viewBox="0 0 24 24"><circle cx="12" cy="8" r="4" fill="#fff"/><path fill="#fff" d="M4 21c0-4.4 3.6-7 8-7s8 2.6 8 7z"/></svg></span>
    <span class="support">SUPPORT</span>
  </div>
</header>

<nav class="main-nav">
  <a class="active" style="left:95px">HOME</a>
  <a style="left:218px">ABOUT US</a>
  <a style="left:376px">SERVICES</a>
  <a style="left:533px">PROJECTS</a>
  <a style="left:695px">CLIENTS</a>
  <a style="left:838px">CAREERS</a>
  <a style="left:988px">CONTACT&nbsp; US</a>
</nav>

<section class="hero" role="img" aria-label="Photograph of a downtown city skyline with office towers under a cloudy sky">
  <div class="hero-tag one">Let Us Worry About Your Technology...</div>
  <div class="hero-tag two">So You Don’t Have To!</div>
  <div class="hero-dots"><span></span><span></span><span></span><span class="on"></span></div>
</section>

<section class="welcome">
  <h1 class="section-title">Welcome to Kelvanbrook <em>Development Group, Inc</em></h1>
  <p>Kelvanbrook Development Group, Inc. was established in 1991. Our mission is helping businesses and individuals realize a Return on Investment by implementing today’s advanced technologies. As a small business we understand the importance of technology and personalized attention.&nbsp; Every member of our support team has worked with both large and small companies supporting a multitude of applications, networks and environments.</p>
  <div class="btn-more">Read More &nbsp;⟶</div>
</section>

<section class="services">
  <h2 class="section-title">Our <em>Services</em></h2>
  <svg width="1200" height="572" viewBox="0 0 1200 572">
    <defs>
      <linearGradient id="svcBlue" x1="0" y1="0" x2="0" y2="1"><stop offset="0" stop-color="#2aa7e8"/><stop offset="1" stop-color="#0f72be"/></linearGradient>
    </defs>
    <!-- dotted connectors -->
    <g stroke="#8d8d8d" stroke-width="1.5" stroke-dasharray="2 3" fill="none">
      <line x1="267" y1="488" x2="375" y2="511"/>
      <line x1="308" y1="378" x2="404" y2="436"/>
      <line x1="385" y1="286" x2="457" y2="374"/>
      <line x1="491" y1="223" x2="530" y2="333"/>
      <line x1="610" y1="195" x2="611" y2="319"/>
      <line x1="726" y1="216" x2="687" y2="332"/>
      <line x1="833" y1="283" x2="762" y2="372"/>
      <line x1="909" y1="378" x2="817" y2="434"/>
      <line x1="951" y1="488" x2="847" y2="510"/>
    </g>
    <!-- semicircle -->
    <path d="M369 572 A242 242 0 0 1 853 572 Z" fill="#fff"/>
    <path d="M369 572 A242 242 0 0 1 853 572" fill="none" stroke="var(--grey-arc)" stroke-width="8"/>
    <g fill="#fff" stroke="#9b9b9b" stroke-width="3">
      <circle cx="375" cy="511" r="7"/><circle cx="404" cy="436" r="7"/><circle cx="457" cy="374" r="7"/>
      <circle cx="530" cy="333" r="7"/><circle cx="611" cy="319" r="7"/><circle cx="687" cy="332" r="7"/>
      <circle cx="762" cy="372" r="7"/><circle cx="817" cy="434" r="7"/><circle cx="847" cy="510" r="7"/>
    </g>
    <rect x="593" y="430" width="30" height="30" rx="5" fill="var(--blue)"/>
    <text x="611" y="505" text-anchor="middle" font-family="'Exo 2',sans-serif" font-weight="800" font-size="34" fill="#6f6f6f">KELVANBROOK</text>

    <!-- icon circles -->
    <g fill="url(#svcBlue)" stroke="#fff" stroke-width="3">
      <circle cx="267" cy="488" r="50"/><circle cx="308" cy="378" r="50"/><circle cx="385" cy="286" r="50"/>
      <circle cx="491" cy="223" r="50"/><circle cx="610" cy="195" r="50"/><circle cx="726" cy="216" r="50"/>
      <circle cx="833" cy="283" r="50"/><circle cx="909" cy="378" r="50"/><circle cx="951" cy="488" r="50"/>
    </g>
    <g fill="none" stroke="#fff" stroke-width="3" stroke-linecap="round" stroke-linejoin="round">
      <!-- desktop support -->
      <rect x="250" y="472" width="34" height="22" rx="2"/><line x1="244" y1="500" x2="290" y2="500"/>
      <!-- network administration -->
      <circle cx="300" cy="366" r="7"/><path d="M287 392c0-8 6-12 13-12s13 4 13 12"/><rect x="313" y="378" width="14" height="10"/>
      <!-- telecommunications -->
      <path d="M385 280 L377 308 M385 280 L393 308 M380 298 h10"/><path d="M373 270a16 16 0 0 0 0 22 M397 270a16 16 0 0 1 0 22 M366 264a26 26 0 0 0 0 34 M404 264a26 26 0 0 1 0 34"/>
      <!-- audio video -->
      <line x1="484" y1="210" x2="484" y2="236" stroke-width="5"/><line x1="498" y1="210" x2="498" y2="236" stroke-width="5"/>
      <!-- disaster recovery -->
      <rect x="594" y="178" width="28" height="9"/><rect x="594" y="189" width="28" height="9"/><rect x="594" y="200" width="20" height="9"/><circle cx="624" cy="208" r="6"/>
      <!-- web design -->
      <rect x="706" y="202" width="30" height="20" rx="2"/><rect x="733" y="210" width="12" height="18" rx="2"/><line x1="712" y1="228" x2="730" y2="228"/>
      <!-- network cabling -->
      <path d="M816 298 l18-18 M828 272 l14 14 -10 10 -14 -14z M840 276 l8-8"/>
      <!-- wireless -->
      <rect x="892" y="382" width="34" height="10" rx="2"/><path d="M898 374a16 16 0 0 1 22 0 M893 367a24 24 0 0 1 32 0"/>
      <!-- antivirus -->
      <path d="M951 468l16 6v12c0 10-7 16-16 20-9-4-16-10-16-20v-12z"/><path d="M956 484a6 6 0 1 0 0 8"/>
    </g>

    <!-- labels -->
    <g class="svc-label">
      <text x="200" y="484" text-anchor="end">DESKTOP</text><text x="200" y="502" text-anchor="end">SUPPORT</text>
      <text x="242" y="364" text-anchor="end">NETWORK</text><text x="242" y="380" text-anchor="end">ADMINISTRATION</text>
      <text x="322" y="276" text-anchor="end">TELECOMMUNICATIONS</text>
      <text x="440" y="200" text-anchor="end">AUDIO/VIDEO MULTIMEDIA</text>
      <text x="610" y="143" text-anchor="middle">DISASTER RECOVERY</text>
      <text x="777" y="191">WEB DESIGN</text>
      <text x="893" y="277">NETWORK CABLING</text>
      <text x="975" y="369">WIRELESS</text><text x="975" y="387">NETWORKS</text>
      <text x="1010" y="480">ANTIVIRUS</text><text x="1010" y="497">SOLUTIONS</text>
    </g>
  </svg>
</section>

<section class="support">
  <h2 class="section-title">IT Support <em>Solution</em></h2>
  <div class="title-rule"></div>
  <svg class="slide-arrow" style="left:36px;top:170px" width="18" height="40" viewBox="0 0 18 40"><path d="M16 2 L3 20 L16 38" fill="none" stroke="#6fb8e6" stroke-width="2"/></svg>
  <svg class="slide-arrow" style="left:1140px;top:170px" width="18" height="40" viewBox="0 0 18 40"><path d="M2 2 L15 20 L2 38" fill="none" stroke="#6fb8e6" stroke-width="2"/></svg>
  <div class="card" style="left:85px">
    <div class="card-photo" role="img" aria-label="Photo of IT technicians working in a server room" style="background:linear-gradient(135deg,#3d5f86,#9fb4c8)"></div>
    <div><h3>Managed IT<br>Solutions</h3><p>Lorem ipsum dolor sit, consectetuer adipiscing elit, sed diam</p></div>
  </div>
  <div class="card" style="left:432px">
    <div class="card-photo" role="img" aria-label="Photo of a support agent with a headset at a laptop" style="background:linear-gradient(135deg,#c9d3dc,#8d9aa6)"></div>
    <div><h3>Remote Diagnostics &amp;<br>Support</h3><p>Lorem ipsum dolor sit, consectetuer adipiscing elit, sed diam</p></div>
  </div>
  <div class="card" style="left:785px">
    <div class="card-photo" role="img" aria-label="Illustration of networked computers connected by cables" style="background:linear-gradient(135deg,#f4f4f4,#e6a070)"></div>
    <div><h3>Infrastructure Design &amp;<br>Installation</h3><p>Lorem ipsum dolor sit, consectetuer adipiscing elit, sed diam</p></div>
  </div>
</section>

<section class="testimonials">
  <h2 class="section-title">Clients <em>Testimonials</em></h2>
  <div class="title-rule"></div>
  <svg class="slide-arrow" style="left:108px;top:188px" width="30" height="56" viewBox="0 0 30 56"><path d="M28 2 L3 28 L28 54" fill="none" stroke="#9a9a9a" stroke-width="1.5"/></svg>
  <svg class="slide-arrow" style="left:1052px;top:188px" width="30" height="56" viewBox="0 0 30 56"><path d="M2 2 L27 28 L2 54" fill="none" stroke="#9a9a9a" stroke-width="1.5"/></svg>
  <span class="quote-mark" style="left:210px;top:128px">“</span>
  <p class="quote">Lorem ipsum dolor sit amet, consectetuer adipiscing elit, sed diam nonummy nibh euismod tinciduntol ut laoreet dolore magna aliquam erat volutpat. Ut wisi enim ad minim veniam, quis nostrud exercimori mornkle tation ullamcorper suscipit lobortis nisl ut aliquip ex ea commodo consequat.</p>
  <span class="quote-mark" style="left:883px;top:190px">”</span>
  <div class="author name">Dana R.</div>
  <div class="author place">Mesa Verde, CA</div>
</section>

<footer class="site-footer" role="img" aria-label="Dark photograph of a city skyline at dusk behind the footer">
  <div class="foot-title" style="left:85px">Quick <em>Links</em></div>
  <div class="foot-rule" style="left:85px;width:125px"></div>
  <ul class="quick-links">
    <li>Home</li><li>About Us</li><li>Services</li><li>Projects</li><li>Clients</li><li>Careers</li><li>Contact Us</li>
  </ul>

  <div class="foot-title" style="left:286px">Contact <em>Details</em></div>
  <div class="foot-rule" style="left:286px;width:250px"></div>
  <div class="contact-block">
    <div>Kelvanbrook Development Group, Inc.</div>
    <div style="margin-top:12px">4120 Marlow St.<br>Houston, Texas 77025</div>
    <div class="contact-row" style="margin-top:18px"><svg width="14" height="14" viewBox="0 0 24 24"><path fill="var(--blue)" d="M6.6 10.8a15 15 0 0 0 6.6 6.6l2.2-2.2c.3-.3.7-.4 1-.2 1.1.4 2.3.6 3.6.6.6 0 1 .4 1 1V20c0 .6-.4 1-1 1A17 17 0 0 1 3 4c0-.6.4-1 1-1h3.5c.6 0 1 .4 1 1 0 1.3.2 2.5.6 3.6.1.3 0 .7-.2 1z"/></svg><span>(713) 555-0148</span></div>
    <div class="contact-row"><svg width="14" height="14" viewBox="0 0 24 24"><rect x="4" y="2" width="16" height="7" fill="var(--blue)"/><rect x="2" y="9" width="20" height="9" rx="2" fill="var(--blue)"/><rect x="6" y="14" width="12" height="8" fill="#fff" stroke="var(--blue)" stroke-width="2"/></svg><span>(713) 555-0148</span></div>
    <div class="contact-row"><svg width="14" height="14" viewBox="0 0 24 24"><rect x="2" y="5" width="20" height="14" fill="var(--blue)"/><path d="M2 5l10 8 10-8" fill="none" stroke="#fff" stroke-width="2"/></svg><span>info@kelvanbrook.com</span></div>
  </div>

  <div class="foot-title" style="left:600px">Quick <em>Inquiry</em></div>
  <div class="foot-rule" style="left:600px;width:225px"></div>
  <div class="form-field" style="top:103px;height:34px;line-height:22px">Name</div>
  <div class="form-field" style="top:141px;height:34px;line-height:22px">Email</div>
  <div class="form-field" style="top:178px;height:60px">Message</div>
  <div class="btn-submit">SUBMIT</div>

  <div class="foot-brand"><span class="brand-square"></span><span>KELVANBROOK</span></div>
</footer>

<div class="bottom-bar">
  <div class="copyright">Copyright © 2017 Kelvanbrook Development Group, Inc. All Rights Reserved.</div>
  <div class="bottom-follow"><span style="margin-right:6px">Follow Us On</span><span class="social"></span><span class="social"></span><span class="social"></span><span class="social"></span></div>
</div>

</body>
</html>
```